Party Favors and Decorations Business Needs A Business Card Design

We are in need of a Logo design and business card design for a new small business called Bright Lantern Designs. We create party decorations and favours for Bridal Showers, Baby Showers, Weddings Birthdays etc. This is a very personalized service based on Clients theme, colour, and style. We are looking for a high end elegant look. I have attached a file to the style I like including the type of paper.

Target Market(s)

women, young adults, expectant mothers, mothers

Industry/Entity Type

Small Business

Contact Information for Business Card

Bright Lantern Favours, ON 519-847-2061 brightlanterndesigns.ca karen@brightlanterngiftbox.com find us on Chatterly

Logo Text

Bright Lantern Designs

Font styles to use
Script

Requirements
Must have
• Name, email, web address, phone number
Should not have
• cutesy graphics

```html
<!DOCTYPE html>
<html lang="en">
<head>
<meta charset="UTF-8">
<title>Bright Lantern Favours — Business Cards</title>
<link rel="stylesheet" href="https://fonts.googleapis.com/css2?family=Lobster+Two:ital,wght@1,700&family=Open+Sans:wght@400;600;700&display=swap">
<style>
  :root {
    --backdrop: #4a423d;
    --card: #151515;
    --card-edge: #1f1f1f;
    --ink: #ffffff;
    --ink-soft: #e4e4e4;
    --rule: #d8d8d8;
  }
  * { box-sizing: border-box; margin: 0; padding: 0; }
  html, body { width: 1200px; height: 780px; overflow: hidden; }
  body {
    background: var(--backdrop);
    font-family: "Open Sans", Arial, sans-serif;
    color: var(--ink);
  }
  .stage {
    position: relative;
    width: 1200px;
    height: 780px;
    display: flex;
    align-items: center;
    justify-content: center;
    gap: 44px;
  }
  .card {
    position: relative;
    width: 520px;
    height: 300px;
    background: radial-gradient(ellipse at 40% 30%, var(--card-edge), var(--card) 70%);
    border-radius: 4px;
    box-shadow: 0 10px 24px rgba(0,0,0,0.45);
  }
  .brand-name {
    font-family: "Open Sans", Arial, sans-serif;
    font-style: normal;
    font-weight: 600;
    color: var(--ink);
    white-space: nowrap;
    letter-spacing: 0.5px;
  }
  .card--front .brand-name {
    position: absolute;
    top: 50%;
    left: 50%;
    transform: translate(-50%, -58%);
    font-size: 34px;
  }
  .card--back .brand-name {
    position: absolute;
    top: 56px;
    left: 0;
    width: 100%;
    text-align: center;
    font-size: 32px;
  }
  .contact {
    position: absolute;
    left: 0;
    right: 0;
    bottom: 46px;
    display: flex;
    justify-content: center;
    align-items: stretch;
  }
  .contact__person {
    text-align: right;
    padding-right: 16px;
  }
  .employee-name {
    font-family: "Lobster Two", "Brush Script MT", cursive;
    font-style: italic;
    font-weight: 700;
    font-size: 22px;
    line-height: 1.15;
  }
  .contact__line {
    font-size: 11.5px;
    color: var(--ink-soft);
    line-height: 1.45;
    letter-spacing: 0.3px;
  }
  .divider {
    width: 1px;
    background: var(--rule);
  }
  .contact__online {
    padding-left: 16px;
    display: flex;
    flex-direction: column;
    justify-content: flex-end;
    gap: 8px;
  }
  .online-item {
    display: flex;
    align-items: center;
    gap: 8px;
  }
  .marker {
    width: 14px;
    height: 14px;
    border-radius: 3px;
    background: var(--ink);
    flex: none;
  }
  .marker--lg { width: 20px; height: 20px; }
  .social__lead {
    font-size: 10px;
    line-height: 1.1;
    color: var(--ink-soft);
  }
  .social__name {
    font-size: 16px;
    font-weight: 700;
    line-height: 1.05;
    color: var(--ink);
  }
</style>
</head>
<body>
  <main class="stage">
    <section class="card card--front" aria-label="Business card front">
      <h1 class="brand-name">Bright Lantern Favours</h1>
    </section>

    <section class="card card--back" aria-label="Business card back">
      <h2 class="brand-name">Bright Lantern Favours</h2>
      <div class="contact">
        <div class="contact__person">
          <p class="employee-name">Employee Name</p>
          <p class="contact__line">519-847-2061</p>
          <p class="contact__line">karen@brightlanterngiftbox.com</p>
        </div>
        <div class="divider" aria-hidden="true"></div>
        <div class="contact__online">
          <div class="online-item">
            <span class="marker" aria-hidden="true"></span>
            <span class="contact__line">brightlanterndesigns.ca</span>
          </div>
          <div class="online-item">
            <span class="marker marker--lg" aria-hidden="true"></span>
            <div>
              <p class="social__lead">Find us on</p>
              <p class="social__name">Chatterly</p>
            </div>
          </div>
        </div>
      </div>
    </section>
  </main>
</body>
</html>
```